Moravel Aesthetic Doctor

I require an elegant, luxurious looking business card for my aesthetic business. I am a doctor and that will set me aside from competitors. I am planning to provide home and spa based treatments to clients with high expectations. I have attached my logo.

```html
<!DOCTYPE html>
<html lang="en">
<head>
<meta charset="utf-8">
<title>Moravel Aesthetic Doctor – Business Card</title>
<link rel="stylesheet" href="https://fonts.googleapis.com/css2?family=Arimo:wght@400;700&display=swap">
<style>
  :root {
    --stage: #ecebe8;
    --card-grey: #a7a9ac;
    --card-white: #ffffff;
    --ink-grey: #8d8f92;
    --brand-blue: #5bb8e6;
    --stripe-blue: #7ccbec;
    --text-white: #ffffff;
  }
  * { box-sizing: border-box; margin: 0; padding: 0; }
  html, body { width: 1200px; height: 900px; overflow: hidden; }
  body {
    background: var(--stage);
    font-family: "Arimo", Arial, sans-serif;
    position: relative;
  }
  .card {
    position: absolute;
    width: 640px;
    height: 390px;
    box-shadow: 0 10px 28px rgba(0,0,0,0.18);
    overflow: hidden;
  }
  /* Back of card */
  .card-back { left: 60px; top: 40px; background: var(--card-grey); color: var(--text-white); }
  .card-back .wordmark { position: absolute; left: 46px; top: 48px; }
  .wordmark-name {
    display: block;
    font-size: 58px;
    font-weight: 400;
    letter-spacing: 6px;
    line-height: 1;
  }
  .wordmark-tag {
    display: block;
    font-size: 21px;
    font-weight: 400;
    letter-spacing: 3px;
    margin-top: 6px;
  }
  .services {
    position: absolute;
    left: 62px;
    top: 214px;
    list-style: none;
    font-size: 15.5px;
    letter-spacing: 1px;
    line-height: 25px;
  }
  .services li::before {
    content: "";
    display: inline-block;
    width: 9px; height: 9px;
    border-radius: 50%;
    background: var(--text-white);
    margin-right: 10px;
    vertical-align: 1px;
  }
  /* Front of card */
  .card-front { left: 500px; top: 470px; background: var(--card-white); }
  .card-front .wave { position: absolute; inset: 0; }
  .holder { position: absolute; left: 40px; top: 60px; }
  .holder-name { font-size: 25px; font-weight: 700; color: var(--ink-grey); }
  .holder-cred { font-size: 15px; font-weight: 400; color: var(--brand-blue); }
  .holder-diploma { font-size: 15px; color: var(--brand-blue); margin-top: 4px; }
  .card-front .wordmark {
    position: absolute; left: 300px; top: 120px;
    display: flex; align-items: center; gap: 14px;
    color: var(--brand-blue);
  }
  .wordmark-ring {
    width: 64px; height: 64px; border-radius: 50%;
    border: 3px solid var(--card-grey); flex: none;
  }
  .card-front .wordmark-name { font-size: 40px; letter-spacing: 4px; }
  .card-front .wordmark-tag { font-size: 15px; letter-spacing: 2px; margin-top: 4px; }
  .contact { position: absolute; left: 86px; top: 232px; list-style: none; color: var(--ink-grey); font-size: 17px; line-height: 28px; }
  .contact li { display: flex; align-items: center; gap: 10px; }
  .contact svg { width: 18px; height: 18px; flex: none; }
  .online { position: absolute; right: 36px; bottom: 40px; text-align: right; color: var(--text-white); font-size: 15px; }
  .channels { display: flex; justify-content: flex-end; gap: 6px; margin-bottom: 8px; }
  .channels span { width: 24px; height: 24px; border-radius: 50%; border: 2px solid var(--text-white); }
</style>
</head>
<body>
  <section class="card card-back" aria-label="Card back">
    <div class="wordmark">
      <span class="wordmark-name">MORAVEL</span>
      <span class="wordmark-tag">AESTHETIC DOCTOR</span>
    </div>
    <ul class="services">
      <li>DERMAL INJECTABLES</li>
      <li>PLASMA FACIALS</li>
      <li>MICRONEEDLING</li>
      <li>SKIN BOOSTERS</li>
      <li>EXCESSIVE SWEATING</li>
      <li>HOME AND SPA BASED TREATMENTS</li>
    </ul>
  </section>

  <section class="card card-front" aria-label="Card front">
    <svg class="wave" viewBox="0 0 640 390" preserveAspectRatio="none" aria-hidden="true">
      <path d="M0,390 L0,322 C220,345 430,210 640,160 L640,390 Z" fill="var(--card-grey)"/>
      <path d="M0,300 C200,318 400,250 560,190 C420,270 220,330 0,322 Z" fill="var(--stripe-blue)"/>
    </svg>
    <div class="holder">
      <p class="holder-name">Dr Elena Varga <span class="holder-cred">MRCPCH MD</span></p>
      <p class="holder-diploma">Australasian Diploma of Aesthetic Medicine</p>
    </div>
    <div class="wordmark">
      <span class="wordmark-ring"></span>
      <div>
        <span class="wordmark-name">MORAVEL</span>
        <span class="wordmark-tag">AESTHETIC DOCTOR</span>
      </div>
    </div>
    <ul class="contact">
      <li>
        <svg viewBox="0 0 24 24" aria-hidden="true"><path d="M6.6 10.8a15 15 0 0 0 6.6 6.6l2.2-2.2a1 1 0 0 1 1-.25 11.4 11.4 0 0 0 3.6.57 1 1 0 0 1 1 1V20a1 1 0 0 1-1 1A17 17 0 0 1 3 4a1 1 0 0 1 1-1h3.5a1 1 0 0 1 1 1c0 1.25.2 2.45.57 3.57a1 1 0 0 1-.25 1z" fill="var(--brand-blue)"/></svg>
        0800 555 014
      </li>
      <li>
        <svg viewBox="0 0 24 24" aria-hidden="true"><rect x="2" y="5" width="20" height="14" fill="var(--brand-blue)"/><path d="M2 5l10 8 10-8" fill="none" stroke="#fff" stroke-width="1.6"/></svg>
        elena@moravel.co.nz
      </li>
    </ul>
    <div class="online">
      <div class="channels"><span></span><span></span><span></span></div>
      www.moravel.co.nz
    </div>
  </section>
</body>
</html>
```